Consulting Website

We are looking at renewing out company's website. we are an organizational development consulting firm that works within the Middle East and Africa. Our focus on on organizations within the Gulf area.

We are looking to having a simple, clean and attractive website. pictures should be relevant to our location.

We are also looking for a creative design, something that isn't just "another consulting website"
Updates

Thank you all for submitting your designs, following are some general comments;

- Having a veiled women on the intro is NOT a must
- have a picture with people is NOT a must too, we can use nature, symbols, places..anything really!
- Here are some sites i like;
brightvale.com
http://www.lanternhomesgroup.com/
http://www.pelicandraft.com/
http://www.morvenli.lk/

I hope these could give you some idea :)

thanks again.

Industry/Entity Type

It Company

Requirements
Must have
• Tabs for press, testimonials, products, resources and services.
pictures also should be relevant to the geographical location. i.e. veiled women, men in traditional costumes and so on.

It's very important that we MAINTAIN the corporate colors of the logo.
Should not have
• Clean and neat design!
i REALLY dont like crowded designs.

```html
<!DOCTYPE html>
<html lang="en">
<head>
<meta charset="utf-8">
<title>Alvaren Consulting</title>
<link rel="stylesheet" href="https://fonts.googleapis.com/css2?family=Open+Sans:wght@400;600;700&family=Cardo&display=swap">
<style>
:root{
  --outer:#64798a;
  --page:#ffffff;
  --ink:#2a2d3e;
  --text:#4a4a52;
  --muted:#3c3c3c;
  --nav-btn:#d3d6d3;
  --nav-band:#e9ebe8;
  --footer:#262a40;
  --footer-text:#c9ccd6;
  --rule:#cfcfcf;
  --blue-a:#5b8fc7;
  --blue-b:#1f5a97;
  --brand-slate:#6a7c88;
  --brand-rose:#c99a8a;
  --brand-sage:#a9b39c;
}
*{margin:0;padding:0;box-sizing:border-box}
html,body{width:1200px;height:1062px;overflow:hidden}
body{background:var(--outer);font-family:"Open Sans",Arial,sans-serif;position:relative}
.page{position:absolute;left:65px;top:0;width:1072px;height:870px;background:var(--page)}
.abs{position:absolute}
.brand{left:96px;top:40px;display:flex;align-items:center;gap:10px}
.brand-mark{width:48px;height:48px;background:var(--brand-slate)}
.brand-name{font-family:"Cardo",Georgia,serif;font-size:34px;color:var(--brand-slate);letter-spacing:1px;line-height:1}
.search{left:826px;top:53px;width:275px;height:31px;border:1px solid #cfd3d6;background:#fff;font-size:13px;color:#223;padding:7px 11px}
.search svg{position:absolute;right:9px;top:7px}
.nav-band{left:115px;top:115px;width:1010px;height:62px;background:linear-gradient(90deg,rgba(233,235,232,0),var(--nav-band) 8%,#f3f4f2 50%,var(--nav-band) 92%,rgba(233,235,232,0))}
.nav{left:264px;top:129px;display:flex;gap:14px;list-style:none}
.nav li{width:101px;height:31px;border-radius:4px;background:var(--nav-btn);text-align:center;line-height:31px;font-size:15px;color:#222}
.slide{left:152px;top:185px;width:886px;height:346px;border:2px solid #d0a296;background:linear-gradient(180deg,#6c87a8 0%,#e0b36a 40%,#9a7b58 62%,#6b5a45 100%)}
.arrow{top:323px}
.intro-title{left:157px;top:554px;font-size:17.5px;font-weight:700;color:var(--ink)}
.intro-body{left:157px;top:596px;width:536px;font-size:12.8px;line-height:18.75px;color:var(--text);letter-spacing:.2px}
.btn-grey{left:527px;top:782px;width:148px;height:29px;border:1px solid #a9a9a9;border-radius:4px;background:linear-gradient(#d6d6d6,#9e9e9e);color:#fff;font-size:13.5px;font-weight:600;padding:5px 0 0 28px}
.btn-grey svg{position:absolute;right:22px;top:9px}
.news-title{left:755px;top:541px;font-family:"Cardo",Georgia,serif;font-size:18px;color:#333}
.rule{left:756px;width:281px;border-top:1px dashed var(--rule)}
.thumb{left:756px;width:54px;height:52px;border:1px solid #c9c9c9;border-radius:4px;background:#fff;padding:4px}
.thumb span{display:block;width:100%;height:100%}
.news-text{left:819px;width:222px;font-family:Arial,sans-serif;font-size:10.6px;line-height:12px;color:var(--muted)}
.btn-blue{height:28px;border-radius:3px;border:1px solid #1a4f86;background:linear-gradient(var(--blue-a),var(--blue-b));color:#fff;font-family:"Cardo",Georgia,serif;font-size:14px;padding:4px 0 0 12px}
.btn-blue svg{position:absolute;right:10px;top:11px}
.footer{left:0;top:870px;width:1200px;height:192px;background:var(--footer)}
.foot-title{font-family:"Cardo",Georgia,serif;font-size:19px;color:#c0c3cc}
.foot-rule{width:308px;border-top:1px dashed #c8cad2}
.foot-text{width:320px;font-size:11px;line-height:16px;color:var(--footer-text)}
.email{left:95px;top:964px;width:308px;height:34px;border:1px solid #bbb;border-radius:4px;background:#fff;font-size:11px;color:#c9c9c9;padding:9px 13px;letter-spacing:.6px}
.social{left:515px;top:967px;display:flex;gap:8px}
.social span{width:42px;height:42px;border-radius:7px}
.foot-brand{left:888px;top:932px;width:245px;height:63px;background:#fff;display:flex;align-items:center;justify-content:center;gap:8px}
.foot-brand .brand-mark{width:36px;height:36px}
.foot-brand .brand-name{font-size:24px}
</style>
</head>
<body>
<div class="page"></div>

<div class="abs brand"><span class="brand-mark"></span><span class="brand-name">ALVAREN</span></div>
<div class="abs search">Search
  <svg width="14" height="14" viewBox="0 0 14 14"><circle cx="5.5" cy="5.5" r="4" fill="none" stroke="#888" stroke-width="1.6"/><line x1="8.5" y1="8.5" x2="13" y2="13" stroke="#888" stroke-width="2"/></svg>
</div>

<div class="abs nav-band"></div>
<ul class="abs nav">
  <li>Home</li><li>About</li><li>Services</li><li>Projects</li><li>News</li><li>Contacts</li>
</ul>

<svg class="abs arrow" style="left:128px" width="22" height="56" viewBox="0 0 22 56"><path d="M22 0 L0 28 L22 56 L18 28Z" fill="#22263c"/></svg>
<div class="abs slide" role="img" aria-label="Panoramic lake at sunset with a twisted old tree on the rocky shore and mountains beyond"></div>
<svg class="abs arrow" style="left:1041px" width="22" height="56" viewBox="0 0 22 56"><path d="M0 0 L22 28 L0 56 L4 28Z" fill="#22263c"/></svg>

<h1 class="abs intro-title">Alvaren Consulting</h1>
<p class="abs intro-body">Alvaren Consulting is a firm specialized in providing customized Organization Development solutions to companies in the Middle East and Africa. Recognizing the inability of imported models and solutions to solve problems that face companies in our region, Alvaren Consulting builds on international best practices and customizes them to create best-fit solutions that are capable of addressing challenges effectively. Alvaren Consulting provides Organization Development solutions addressing the "HOW – Soft Side" that is needed to achieve the "WHAT – Business Strategy" in a holistic manner. Alvaren Consulting work centers around building an organizational culture that is aligned with and supports the business strategy.</p>
<div class="abs btn-grey">Read more
  <svg width="14" height="12" viewBox="0 0 14 12"><path d="M0 0 L14 6 L0 12 L3 6Z" fill="#fff"/></svg>
</div>

<h2 class="abs news-title">News Updates</h2>
<div class="abs rule" style="top:568px"></div>
<div class="abs thumb" style="top:580px"><span style="background:#3b3f8e"></span></div>
<p class="abs news-text" style="top:580px">Lorem ipsum dolor sit amet, consectetur adipisicing elit, sed do eiusmod tempor incididunt ut labore et dolore magna aliqua.</p>
<div class="abs rule" style="top:639px"></div>
<div class="abs thumb" style="top:652px"><span role="img" aria-label="Abstract glowing purple spheres" style="background:radial-gradient(circle,#e040c8,#5a0a5a)"></span></div>
<p class="abs news-text" style="top:652px">Sed ut perspiciatis unde omnis iste natus error sit voluptatem accusantium doloremque laudantium, totam rem aperiam.</p>
<div class="abs rule" style="top:710px"></div>
<div class="abs thumb" style="top:724px"><span role="img" aria-label="Abstract colourful waves" style="background:linear-gradient(160deg,#5bc0e0,#f4e04a 50%,#d84a9a)"></span></div>
<p class="abs news-text" style="top:724px">At vero eos et accusamus et iusto odio dignissimos ducimus qui blanditiis praesentium.</p>
<div class="abs rule" style="top:784px"></div>
<div class="abs btn-blue" style="left:756px;top:794px;width:155px">Visit our Blog
  <svg width="22" height="6" viewBox="0 0 22 6"><path d="M0 3H20M17 0L21 3L17 6" stroke="#fff" fill="none"/></svg>
</div>

<footer class="abs footer"></footer>
<h3 class="abs foot-title" style="left:94px;top:880px">Newsletter</h3>
<div class="abs foot-rule" style="left:95px;top:909px"></div>
<p class="abs foot-text" style="left:95px;top:921px">At vero eos et accusamus et iusto odio dignissimos ducimus qui blanditiis praesentium</p>
<div class="abs email">your email address</div>
<div class="abs btn-blue" style="left:96px;top:1010px;width:168px;height:32px;padding-top:6px">Subscribe
  <svg width="22" height="6" viewBox="0 0 22 6"><path d="M0 3H20M17 0L21 3L17 6" stroke="#fff" fill="none"/></svg>
</div>

<h3 class="abs foot-title" style="left:493px;top:880px">Social Connection</h3>
<div class="abs foot-rule" style="left:495px;top:909px"></div>
<p class="abs foot-text" style="left:497px;top:919px">At vero eos et accusamus et iusto odio dignissimos ducimus qui blanditiis praesentium</p>
<div class="abs social">
  <span style="background:#e8602a"></span>
  <span style="background:#3f6aa5"></span>
  <span style="background:#3f8cc4"></span>
  <span style="background:#c8262a"></span>
  <span style="background:#4fb8d0"></span>
</div>

<div class="abs foot-brand"><span class="brand-mark"></span><span class="brand-name">ALVAREN</span></div>
</body>
</html>
```